Business Cards for a law firm

Business cards for our law firm. Use our silhoette logo and OAK PARTNERS - check our website (www.oakpartners.example)

Contact Information for Business Card

our silhouette logo, OAK PARTNERS, 800-555-0147, Dorian Pemberton, dorian@oakpartners.example

Requirements
Must have
• our silhouette logo, OAK PARTNERS, 800-555-0147, Dorian Pemberton, dorian@oakpartners.example

```html
<!DOCTYPE html>
<html lang="en">
<head>
<meta charset="utf-8">
<title>Oak Partners — Business Cards</title>
<link href="https://fonts.googleapis.com/css2?family=Arimo:wght@400;700&display=swap" rel="stylesheet">
<style>
  :root {
    --backdrop: #9a9a9a;
    --paper: #f7f7f5;
    --navy: #172c66;
    --navy-text: #2a3f8a;
    --ink: #3a3a3a;
    --rule: #555555;
    --white: #ffffff;
  }
  * { margin: 0; padding: 0; box-sizing: border-box; }
  html, body {
    width: 1200px;
    height: 1050px;
    overflow: hidden;
    background: var(--backdrop);
    font-family: "Arimo", Arial, sans-serif;
  }
  .stage { position: relative; width: 1200px; height: 1050px; }

  .card {
    position: absolute;
    border-radius: 22px;
    box-shadow: 0 6px 18px rgba(0,0,0,0.18);
  }

  /* Front: portrait, white */
  .card-front {
    left: 110px;
    top: 215px;
    width: 360px;
    height: 620px;
    background: var(--paper);
    display: flex;
    flex-direction: column;
    align-items: center;
    padding-top: 150px;
  }
  .front-brand {
    display: flex;
    align-items: center;
    gap: 10px;
    color: var(--navy-text);
    font-weight: 700;
    font-size: 20px;
    letter-spacing: 2px;
  }
  .brand-square {
    width: 16px;
    height: 16px;
    background: currentColor;
  }
  .front-details {
    margin-top: 60px;
    width: 240px;
  }
  .person-name {
    color: var(--navy-text);
    font-weight: 700;
    font-size: 22px;
    letter-spacing: 0.5px;
    text-transform: uppercase;
  }
  .name-rule {
    width: 84px;
    height: 1px;
    background: var(--rule);
    margin: 26px 0 26px 120px;
  }
  .contact-list { list-style: none; }
  .contact-list li {
    font-size: 15px;
    color: var(--ink);
    line-height: 26px;
    white-space: nowrap;
  }
  .contact-label {
    color: var(--navy-text);
    font-weight: 700;
    display: inline-block;
    width: 28px;
  }

  /* Back: landscape, navy */
  .card-back {
    left: 530px;
    top: 355px;
    width: 600px;
    height: 345px;
    background: var(--navy);
    border: 2px solid var(--white);
    display: flex;
    align-items: center;
    justify-content: center;
  }
  .back-brand {
    display: flex;
    align-items: center;
    gap: 18px;
    color: var(--white);
    font-weight: 700;
    font-size: 34px;
    letter-spacing: 4px;
  }
  .back-brand .brand-square { width: 26px; height: 26px; }
</style>
</head>
<body>
  <main class="stage">
    <section class="card card-front" aria-label="Business card front">
      <div class="front-brand">
        <span class="brand-square" aria-hidden="true"></span>
        <span>OAK PARTNERS</span>
      </div>
      <div class="front-details">
        <h1 class="person-name">Dorian Pemberton</h1>
        <div class="name-rule"></div>
        <ul class="contact-list">
          <li><span class="contact-label">P :</span>800-555-0147</li>
          <li><span class="contact-label">E :</span>dorian@oakpartners.example</li>
          <li><span class="contact-label">W :</span>www.oakpartners.example</li>
        </ul>
      </div>
    </section>

    <section class="card card-back" aria-label="Business card back">
      <div class="back-brand">
        <span class="brand-square" aria-hidden="true"></span>
        <span>OAK PARTNERS</span>
      </div>
    </section>
  </main>
</body>
</html>
```